Bright and beautiful business card for a coach

I'm a personal and business coach based in Perth, Australia. I need a business card that whilst subtle and elegant, will stand out and appeal on a table full of cards.

My business name is Fern Mentoring and the business card must represent the warmth and brightness implied in the name, without being gimmicky. It must have a warmth and appeal and be easy to read.

I prefer clean, minimalist designs.

It must align with the feel of my website and socials: https://www.fernmentoring-example.com.au/
https://www.instagram.com/fernmentoringau/
https://www.facebook.com/fernmentoringau
Updates

Hi Designers Thank you so much for taking the time to submit designs. I wonder if I could have explained myself a little better. Most of the designs that have been submitted look rather formal and many have quite corporate looking embellishments on them (to my eye). I would like softer, warmer, more organic. I’m open to people playing about and being more abstract, using softer embellishments (e.g the line drawing flowers and grasses I’ve used in my socials) incorporating other colours from my palette or like the social icons in my email signature (in PDF), perhaps playing with size/oversize, playing with the bleed. Please don’t be constrained by what I’ve already done, it merely needs to compliment. I’m sorry if I’m not using the right words or have led you astray. I’m no designer, but I’ve done my website, socials, email signature etc all myself (my logo was a design contest) and I was really hoping for my business card to be something more creative than I could have made with a template. Reminder: No black cards/sides please. Thank you 😊

Target Market(s)

Individuals, most likely but not all female. Creative thinkers. Likely professionals.

Industry/Entity Type

Business & Personal Coach

Contact Information for Business Card

(Fern Mentoring Logo) Name: Greta Pellham; Title: Business & Personal Coach; Phone number: +61 (0)458 913307; Email: greta@fernmentoring-example.com.au; Website: https://fernmentoring-example.com.au; Social icons for Facebook, Instagram & LinkedIn: @fernmentoringAU. Optional strapline: "A thinking partner to help you cut through the noise"

Font styles to use
Sans Serif

Colors
00AB8E
00BBA5
67D7C9
C6EFE9
E9F9F6
59FF00
82FF00
B8FF75
E3FFCB
F4FFEA
FFC000
F8CF3A
FAE287
FDF2CF
FEFAEE

Requirements
Must have
• Must align with feel of my website and socials. Must have a pop of #FFC000 (possibly whole of one side, or at least a block). Bright or white background. Easy to read.
Nice to have
• Possibly incorporate the sunshine/grass picture I have used in website and socials - will upload.
Should not have
• Must not be black or dark. Not impersonal or corporate looking.

```html
<!DOCTYPE html>
<html lang="en">
<head>
<meta charset="utf-8">
<title>Fern Mentoring – Business Card</title>
<link href="https://fonts.googleapis.com/css2?family=Montserrat:wght@300;400;500;700&display=swap" rel="stylesheet">
<style>
  :root {
    --backdrop: #e4e5e7;
    --card-light: #fefaee;
    --sun: #ffc000;
    --sun-deep: #c98a00;
    --sun-soft: #fae287;
    --ink: #3a3a3c;
    --ink-soft: #5e5f62;
    --white: #ffffff;
  }
  * { box-sizing: border-box; margin: 0; padding: 0; }
  html, body {
    width: 1200px; height: 800px; overflow: hidden;
    background: var(--backdrop);
    font-family: "Montserrat", sans-serif;
  }
  .canvas { position: relative; width: 1200px; height: 800px; }

  .card {
    position: absolute; top: 242px;
    width: 540px; height: 316px;
    border-radius: 22px;
    overflow: hidden;
    box-shadow: 0 10px 28px rgba(0,0,0,0.12);
  }
  .card--front { left: 40px; background: var(--card-light); border-bottom: 3px solid var(--sun); }
  .card--back { left: 620px; background: var(--sun); }

  /* front */
  .front__brand {
    position: absolute; right: 40px; top: 70px;
    font-size: 22px; font-weight: 400; letter-spacing: 2px;
    color: var(--sun-deep);
  }
  .front__name {
    position: absolute; left: 34px; top: 128px;
    font-size: 22px; font-weight: 700; color: var(--sun-deep);
  }
  .front__title {
    position: absolute; left: 34px; top: 160px;
    font-size: 13px; font-weight: 400; color: var(--ink-soft);
  }
  .front__divider {
    position: absolute; left: 30px; right: 22px; top: 186px;
    height: 1px; background: var(--sun);
  }
  .contact-list {
    position: absolute; left: 34px; top: 200px;
    list-style: none;
  }
  .contact-list li {
    display: flex; align-items: center; gap: 10px;
    font-size: 13px; font-weight: 400; color: var(--ink);
    line-height: 24px;
  }
  .contact-list svg { width: 13px; height: 13px; flex: none; }

  /* back */
  .back__brand {
    position: absolute; left: 0; right: 0; top: 118px;
    text-align: center;
    font-size: 32px; font-weight: 300; letter-spacing: 4px;
    color: var(--ink);
  }
  .back__social {
    position: absolute; left: 0; right: 0; top: 232px;
    display: flex; justify-content: center; align-items: center; gap: 8px;
    font-size: 14px; font-weight: 400; color: var(--ink);
  }
  .back__social-dot {
    width: 14px; height: 14px; border-radius: 50%;
    background: var(--white);
  }
</style>
</head>
<body>
<main class="canvas">

  <section class="card card--front" aria-label="Card front">
    <div class="front__brand">Fern Mentoring</div>
    <h1 class="front__name">Greta Pellham</h1>
    <p class="front__title">Business &amp; Personal Coach</p>
    <div class="front__divider"></div>
    <ul class="contact-list">
      <li>
        <svg viewBox="0 0 24 24" aria-hidden="true"><path fill="#ffc000" d="M6.6 10.8a15 15 0 0 0 6.6 6.6l2.2-2.2a1 1 0 0 1 1-.25 11.4 11.4 0 0 0 3.6.57 1 1 0 0 1 1 1V20a1 1 0 0 1-1 1A17 17 0 0 1 3 4a1 1 0 0 1 1-1h3.5a1 1 0 0 1 1 1c0 1.25.2 2.45.57 3.57a1 1 0 0 1-.25 1z"/></svg>
        +61 (0)458 913307
      </li>
      <li>
        <svg viewBox="0 0 24 24" aria-hidden="true"><rect x="2" y="5" width="20" height="14" rx="2" fill="#ffc000"/><path d="M3 6l9 7 9-7" fill="none" stroke="#fefaee" stroke-width="2"/></svg>
        greta@fernmentoring-example.com.au
      </li>
      <li>
        <svg viewBox="0 0 24 24" aria-hidden="true"><circle cx="12" cy="12" r="10" fill="#ffc000"/><path d="M2 12h20M12 2c3 3 3 17 0 20M12 2c-3 3-3 17 0 20" fill="none" stroke="#fefaee" stroke-width="1.6"/></svg>
        www.fernmentoring-example.com.au
      </li>
    </ul>
  </section>

  <section class="card card--back" aria-label="Card back">
    <div class="back__brand">Fern Mentoring</div>
    <div class="back__social">
      <span class="back__social-dot" aria-hidden="true"></span>
      @fernmentoringAU
    </div>
  </section>

</main>
</body>
</html>
```